Home Remodeling company needs a business card design

we need a business card design for home remodeling company in hamilton county, indiana USA. we offers a wide range of construction services including whole house renovations, Design and Build Basements and Kitchen and Bathroom Remodeling . we would like to see designs for both site of business card that use the same color of the company logo and also including all information below :
1- Karim Feltous CEO / General Contractor
2- all company contacts Telephone numbers ( 1-888-DULOM-47 ) ( 317-555-0193) email address ( info@dulomhome.com) website ( www.dulomhome.com ) and social media logos (Facebook- twitter- google plus )
3- company logo
4- licensed . insured . bonded

```html
<!DOCTYPE html>
<html lang="en">
<head>
<meta charset="UTF-8">
<title>Dulom Home Remodeling – Business Card</title>
<link rel="stylesheet" href="https://fonts.googleapis.com/css2?family=Roboto:wght@400;500;700&display=swap">
<style>
  :root {
    --stage: #3b3230;
    --card-black: #1a1a1c;
    --card-black-2: #262628;
    --brand-red: #d8221f;
    --white: #f4f4f4;
    --grey: #b9b9b9;
    --emboss: #3e3e40;
    --icon-grey: #8a8a8c;
  }
  * { margin: 0; padding: 0; box-sizing: border-box; }
  html, body { width: 1200px; height: 716px; overflow: hidden; }
  body {
    background: var(--stage);
    font-family: "Roboto", Arial, sans-serif;
    position: relative;
  }
  .card {
    position: absolute;
    top: 208px;
    width: 525px;
    height: 300px;
    border-radius: 4px;
    overflow: hidden;
    box-shadow: 0 10px 30px rgba(0,0,0,.45);
  }
  .card--back { left: 45px; background: var(--card-black); }
  .card--front {
    left: 630px;
    background: linear-gradient(160deg, var(--card-black-2), var(--card-black) 70%);
  }
  .card__art { position: absolute; inset: 0; }

  .company-name {
    position: absolute;
    display: flex;
    align-items: center;
    gap: 12px;
    font-family: "Roboto", Arial, sans-serif;
    font-weight: 700;
    font-size: 28px;
    line-height: 1.1;
  }
  .company-name__square { width: 14px; height: 14px; flex: none; }

  .card--back .company-name {
    left: 50%; top: 50%;
    transform: translate(-50%, -50%);
    color: var(--emboss);
  }
  .card--back .company-name__square { background: var(--emboss); }

  .card--front .company-name { left: 24px; top: 44px; color: var(--white); }
  .card--front .company-name__square { background: var(--white); }

  .person { position: absolute; left: 24px; top: 140px; }
  .person__name { color: var(--brand-red); font-size: 19px; font-weight: 500; }
  .person__role { color: var(--grey); font-size: 12px; margin-top: 3px; }
  .social { display: flex; gap: 5px; margin-top: 9px; }
  .social__spot { width: 13px; height: 13px; border-radius: 50%; background: var(--icon-grey); }

  .credentials {
    position: absolute; right: 18px; top: 82px;
    color: var(--white); font-size: 13px; text-align: right; line-height: 1.3;
  }

  .contacts {
    position: absolute; left: 300px; top: 192px;
    list-style: none; color: var(--white); font-size: 14px; line-height: 1.45;
  }
  .contacts li { display: flex; align-items: center; gap: 12px; }
  .contacts svg { width: 10px; height: 10px; fill: var(--brand-red); flex: none; }
</style>
</head>
<body>

<section class="card card--back" aria-label="Card back">
  <div class="company-name">
    <span class="company-name__square"></span>
    <div>Dulom<br>Home Remodeling</div>
  </div>
</section>

<section class="card card--front" aria-label="Card front">
  <svg class="card__art" viewBox="0 0 525 300" preserveAspectRatio="none" aria-hidden="true">
    <path d="M0 0 H525 V240 C445 215 390 150 320 85 C250 25 120 18 0 22 Z" fill="var(--brand-red)"/>
    <path d="M0 22 C120 18 250 25 320 85 C390 150 445 215 525 240" fill="none" stroke="var(--white)" stroke-width="9"/>
    <path d="M30 34 C150 30 270 45 340 110 C400 165 450 220 525 252" fill="none" stroke="var(--white)" stroke-width="2.5"/>
  </svg>

  <div class="company-name">
    <span class="company-name__square"></span>
    <div>Dulom<br>Home Remodeling</div>
  </div>

  <div class="person">
    <div class="person__name">Karim Feltous</div>
    <div class="person__role">CEO / General Contractor</div>
    <div class="social">
      <span class="social__spot" role="img" aria-label="Social media link"></span>
      <span class="social__spot" role="img" aria-label="Social media link"></span>
      <span class="social__spot" role="img" aria-label="Social media link"></span>
    </div>
  </div>

  <div class="credentials">
    <div>Licensed «</div>
    <div>Bonded «</div>
    <div>Insured «</div>
  </div>

  <ul class="contacts">
    <li><svg viewBox="0 0 10 10"><path d="M2 0 L4 2 L3 3.5 Q4.5 5.5 6.5 7 L8 6 L10 8 L8.5 10 Q3 9 0 1.5 Z"/></svg>1-888-DULOM-47</li>
    <li><svg viewBox="0 0 10 10"><rect x="0" y="2" width="10" height="8" rx="1"/><rect x="2" y="0" width="6" height="3"/></svg>317-555-0193</li>
    <li><svg viewBox="0 0 10 10"><path d="M0 2 H10 V9 H0 Z M0 2 L5 6 L10 2" stroke="var(--card-black)" stroke-width=".8"/></svg>info@dulomhome.com</li>
    <li><svg viewBox="0 0 10 10"><circle cx="5" cy="5" r="5"/></svg>www.dulomhome.com</li>
  </ul>
</section>

</body>
</html>
```